female esthetician looking for an impact business card

I an an expert in skin care industry with high experience in NYC.I want my business card to look professional , an impact at first look. I do want a combination between white and gold . I believe the font will be great if is gold.. The Fonts are also important. MIRABELA COSTINA (SKIN CARE BOUTIQUE)

THIS SHOULD BE THE BUSINESS NAME, and should be placed on th eback of the card.
IN front m, the name MIRABELA COSTINA - ESTHETCIAN

BY APPOINTMENTS ONLY: 518.240.7136

Target Market(s)

HIGH END CLIENTELE

Contact Information for Business Card

iT WILL BE on a luxury paper. I neeed the wow feeling

Requirements
Should not have
• pictures

```html
<!DOCTYPE html>
<html lang="en">
<head>
<meta charset="utf-8">
<title>Mirabela Costina – Business Card</title>
<link href="https://fonts.googleapis.com/css2?family=Cinzel:wght@400;500&display=swap" rel="stylesheet">
<style>
  :root {
    --backdrop: #dddddd;
    --paper: #ffffff;
    --gold: #d9ae7f;
    --gold-ink: #d4a66f;
    --ivory: #ffffff;
  }
  * { margin: 0; padding: 0; box-sizing: border-box; }
  html, body {
    width: 1200px;
    height: 897px;
    overflow: hidden;
    background: var(--backdrop);
  }
  .canvas {
    position: relative;
    width: 1200px;
    height: 897px;
    font-family: "Cinzel", "Trajan Pro", serif;
  }
  .card {
    position: absolute;
    left: 329px;
    width: 543px;
    height: 310px;
  }
  .card--front { top: 108px; background: var(--paper); }
  .card--back  { top: 479px; background: var(--gold); }

  .front-info {
    position: absolute;
    left: 26px;
    top: 111px;
    color: var(--gold-ink);
  }
  .holder-name {
    font-size: 28px;
    font-weight: 500;
    line-height: 1;
    letter-spacing: 0.3px;
  }
  .holder-role {
    font-size: 14px;
    margin-top: 5px;
    letter-spacing: 0.3px;
  }
  .address {
    font-size: 14.5px;
    line-height: 22px;
    margin-top: 12px;
  }
  .contact {
    margin-top: 9px;
    font-size: 13.5px;
    line-height: 22px;
    border-collapse: collapse;
  }
  .contact td { padding: 0; vertical-align: baseline; }
  .contact .label { width: 54px; }
  .contact .sep { width: 11px; }

  .brand-name {
    position: absolute;
    left: 0;
    right: 0;
    top: 138px;
    text-align: center;
    color: var(--ivory);
    font-size: 29px;
    font-weight: 500;
    line-height: 1;
    letter-spacing: 0.5px;
  }
</style>
</head>
<body>
<main class="canvas">
  <section class="card card--front">
    <div class="front-info">
      <h1 class="holder-name">MIRABELA COSTINA</h1>
      <p class="holder-role">Skin care expert</p>
      <p class="address">142b Linden Avenue,<br>Brookhaven, NY, 10583</p>
      <table class="contact">
        <tr><td class="label">Phone</td><td class="sep">:</td><td>(518) 240-7136</td></tr>
        <tr><td class="label">Email</td><td class="sep">:</td><td>info@mirabelacostina.com</td></tr>
        <tr><td class="label">Web</td><td class="sep">:</td><td>www.mirabelacostina.com</td></tr>
      </table>
    </div>
  </section>

  <section class="card card--back">
    <h2 class="brand-name">MIRABELA COSTINA</h2>
  </section>
</main>
</body>
</html>
```